High-end construction company needs a business card design

We need a modern looking business card that draws people in, is memorable and looks so good people will want to sick it on their fridges.
On the first side what is needed are:
Logo
My name - Tomasz Brelwik
Title - Managing Director
Website - www.varkelt.co.uk
Email - tomasz@varkelt.co.uk
Telephone - 020 5194 6281
Mobile - 07845139072
On the back side was is needed is a list of all the services we provide:
-Kitchen Renovations
-Bathroom Renovations
-House Renovations
-Garage Conversions
-Extensions
-Loft Conversions
-Conservatories
-Carpentry
-Tiling
-Electrical
-Plumbing & Heating
-Bricklaying
-Landscaping
-Decorating
-Plastering
We would like the colours to be the same shades as on the logo with grey or black for the words.
Target Market(s)
Anyone who needs building work done
Contact Information for Business Card
This business card is for a construction company which strives to deliver excellent service and quality.
The look and feel of the card should represent this.
Requirements
Must have
- On the first side what is needed are:
Logo
My name - Tomasz Brelwik
Title - Managing Director
Website - www.varkelt.co.uk
Email - tomasz@varkelt.co.uk
Telephone - 020 5194 6281
Mobile - 07845139072
Nice to have
- Cool looking features

```html
<!DOCTYPE html>
<html lang="en">
<head>
<meta charset="utf-8">
<title>Varkelt Construction Ltd – Business Card</title>
<link rel="stylesheet" href="https://fonts.googleapis.com/css2?family=Montserrat:wght@700;800&family=Questrial&display=swap">
<style>
  :root {
    --backdrop: #1f1f1f;
    --brand-green: #4d8e3f;
    --brand-green-light: #72bf44;
    --brand-green-dark: #3b8a36;
    --card-white: #ffffff;
    --text-white: #ffffff;
    --text-grey: #333333;
    --rule-green: #7fc94f;
  }
  * { box-sizing: border-box; margin: 0; padding: 0; }
  html, body {
    width: 1200px; height: 988px; overflow: hidden;
    background: var(--backdrop);
  }
  .canvas { position: relative; width: 1200px; height: 988px; }

  .card {
    position: absolute;
    width: 600px; height: 360px;
    border-radius: 22px;
    overflow: hidden;
  }

  /* Services side */
  .card--services {
    left: 50px; top: 110px;
    background: var(--brand-green);
    color: var(--text-white);
    text-align: center;
  }
  .services__brand {
    position: absolute; top: 86px; left: 0; right: 0;
    font-family: "Montserrat", sans-serif; font-weight: 800;
    font-size: 34px; letter-spacing: 1px; text-transform: uppercase;
    color: var(--text-white);
  }
  .services__heading {
    position: absolute; top: 186px; left: 40px; right: 40px;
    display: flex; align-items: center; gap: 16px;
    font-family: "Montserrat", sans-serif; font-weight: 800;
    font-size: 15px; letter-spacing: 1.5px;
  }
  .services__heading::before,
  .services__heading::after {
    content: ""; flex: 1; height: 1px; background: var(--rule-green);
  }
  .services__list {
    position: absolute; top: 228px; left: 20px; right: 20px;
    font-family: "Questrial", sans-serif; font-size: 14.5px; line-height: 25px;
    list-style: none;
  }
  .services__list .dot { color: var(--rule-green); padding: 0 4px; }

  /* Contact side */
  .card--contact {
    left: 550px; top: 520px;
    background: var(--card-white);
  }
  .contact__accent {
    position: absolute; left: 0; top: 122px;
    width: 26px; height: 34px; background: var(--brand-green-light);
  }
  .contact__name {
    position: absolute; left: 48px; top: 112px;
    font-family: "Montserrat", sans-serif; font-weight: 800;
    font-size: 30px; letter-spacing: 0.5px; text-transform: uppercase;
  }
  .contact__name .first { color: var(--brand-green-light); }
  .contact__name .last { color: var(--brand-green-dark); }
  .contact__title {
    position: absolute; left: 50px; top: 154px;
    font-family: "Questrial", sans-serif; font-size: 17px; color: var(--text-grey);
  }
  .contact__list {
    position: absolute; left: 50px; top: 222px;
    list-style: none;
    font-family: "Questrial", sans-serif; font-size: 17px; color: var(--text-grey);
  }
  .contact__list li { display: flex; align-items: center; gap: 9px; height: 27px; }
  .contact__list svg { width: 15px; height: 15px; fill: var(--brand-green-light); flex: none; }
  .contact__brand {
    position: absolute; right: 34px; top: 110px; width: 230px;
    text-align: center;
    font-family: "Montserrat", sans-serif; font-weight: 800;
    font-size: 26px; line-height: 32px; text-transform: uppercase;
    color: var(--brand-green-light);
  }
</style>
</head>
<body>
<main class="canvas">

  <section class="card card--services" aria-label="Business card back: services">
    <div class="services__brand">Varkelt Construction Ltd</div>
    <h2 class="services__heading">OUR SERVICES</h2>
    <ul class="services__list">
      <li>Kitchen Renovations<span class="dot">•</span>Bathroom Renovations<span class="dot">•</span>House Renovations<span class="dot">•</span>Extensions</li>
      <li>Garage Conversions<span class="dot">•</span>Loft Conversions<span class="dot">•</span>Conservatories<span class="dot">•</span>Carpentry<span class="dot">•</span>Electrical</li>
      <li>Plumbing &amp; Heating<span class="dot">•</span>Bricklaying<span class="dot">•</span>Landscaping<span class="dot">•</span>Decorating<span class="dot">•</span>Plastering<span class="dot">•</span>Tiling</li>
    </ul>
  </section>

  <section class="card card--contact" aria-label="Business card front: contact">
    <div class="contact__accent"></div>
    <h1 class="contact__name"><span class="first">Tomasz</span> <span class="last">Brelwik</span></h1>
    <p class="contact__title">Managing Director</p>
    <ul class="contact__list">
      <li>
        <svg viewBox="0 0 16 16" aria-hidden="true"><path d="M1 5c0-2 3-3 7-3s7 1 7 3v1.5h-3.5V5h-7v1.5H1z"/><rect x="3" y="7.5" width="10" height="6.5" rx="1.5"/></svg>
        020 5194 6281
      </li>
      <li>
        <svg viewBox="0 0 16 16" aria-hidden="true"><path d="M4.5 1h7a1 1 0 0 1 1 1v12a1 1 0 0 1-1 1h-7a1 1 0 0 1-1-1V2a1 1 0 0 1 1-1zm.8 2v9h5.4V3zM8 12.6a.8.8 0 1 0 0 1.6.8.8 0 0 0 0-1.6z"/></svg>
        07845139072
      </li>
      <li>
        <svg viewBox="0 0 16 16" aria-hidden="true"><path d="M1 3.5h14v9H1z M1.5 4 8 9l6.5-5" stroke="#fff" stroke-width="1"/></svg>
        tomasz@varkelt.co.uk
      </li>
      <li>
        <svg viewBox="0 0 16 16" aria-hidden="true"><circle cx="8" cy="8" r="7"/><path d="M5 4c1 1 2 1 2 3S5 8 4.5 10M10 3.5c-1 1.5 1 2.5 2.5 2.5M10 13c0-2 2-2 2.5-3.5" stroke="#fff" stroke-width="1.2" fill="none"/></svg>
        www.varkelt.co.uk
      </li>
    </ul>
    <div class="contact__brand">Varkelt Construction Ltd</div>
  </section>

</main>
</body>
</html>
```